Structural Engineering Business Card

Brookvane Drafting does residential house plans for clients in Central Florida. Would like simple but elegant business card that is appropriate for a house plan engineering company. Prefer black business card with black/white them but open to other shades of blue. I uploaded a sample card that I came across that looked good but please come up with your own creative designs.

Contact Information for Business Card

Name, Title, Phone, Email, Address, website

```html
<!DOCTYPE html>
<html lang="en">
<head>
<meta charset="utf-8">
<title>Brookvane Drafting – Business Card</title>
<link href="https://fonts.googleapis.com/css2?family=Montserrat:wght@700;800&family=Varela+Round&display=swap" rel="stylesheet">
<style>
  :root {
    --backdrop: #cfcfcf;
    --card: #ffffff;
    --ink: #111111;
    --ink-soft: #555555;
    --shadow: rgba(0, 0, 0, 0.18);
  }
  html, body {
    margin: 0;
    padding: 0;
    width: 1200px;
    height: 1200px;
    overflow: hidden;
    background: var(--backdrop);
  }
  .canvas {
    position: relative;
    width: 1200px;
    height: 1200px;
  }
  .card {
    position: absolute;
    left: 240px;
    width: 720px;
    height: 411px;
    background: var(--card);
    box-shadow: 0 10px 30px var(--shadow);
  }
  .card--front { top: 150px; }
  .card--back { top: 640px; }

  /* Front face */
  .identity {
    position: absolute;
    left: 120px;
    top: 120px;
    width: 230px;
    text-align: right;
  }
  .identity__name {
    margin: 0;
    font-family: "Montserrat", sans-serif;
    font-weight: 800;
    font-size: 23px;
    letter-spacing: 0.5px;
    color: var(--ink);
  }
  .identity__title {
    margin: 2px 0 0;
    font-family: "Varela Round", sans-serif;
    font-size: 17px;
    color: var(--ink-soft);
  }
  .contacts {
    position: absolute;
    left: 380px;
    top: 146px;
    margin: 0;
    padding: 0;
    list-style: none;
    font-family: "Varela Round", sans-serif;
    font-size: 19px;
    color: var(--ink-soft);
  }
  .contacts__item {
    display: flex;
    align-items: center;
    gap: 10px;
    height: 30px;
  }
  .contacts__icon {
    width: 20px;
    height: 20px;
    flex: none;
  }
  .address {
    position: absolute;
    left: 150px;
    top: 262px;
    margin: 0;
    font-family: "Varela Round", sans-serif;
    font-size: 19px;
    color: var(--ink-soft);
  }

  /* Back face */
  .brand {
    position: absolute;
    inset: 0;
    display: flex;
    align-items: center;
    justify-content: center;
  }
  .brand__name {
    margin: 0;
    font-family: "Montserrat", sans-serif;
    font-weight: 800;
    font-size: 50px;
    letter-spacing: 1px;
    color: var(--ink);
    text-transform: uppercase;
  }
</style>
</head>
<body>
<main class="canvas">
  <section class="card card--front" aria-label="Business card front">
    <div class="identity">
      <h1 class="identity__name">DORIAN WEXLEY</h1>
      <p class="identity__title">Owner</p>
    </div>
    <ul class="contacts">
      <li class="contacts__item">
        <svg class="contacts__icon" viewBox="0 0 20 20" aria-hidden="true">
          <circle cx="10" cy="10" r="10" fill="#111"/>
          <path d="M6.5 5.5c.6-.5 1.3-.4 1.6.2l.8 1.5c.2.5 0 1-.4 1.3l-.5.4c.5 1.2 1.4 2.1 2.6 2.6l.4-.5c.3-.4.8-.6 1.3-.4l1.5.8c.6.3.7 1 .2 1.6l-.6.6c-.7.7-1.9.8-3 .2C8.5 12.7 7.3 11.5 6.2 9.6c-.6-1.1-.5-2.3.2-3z" fill="#fff"/>
        </svg>
        <span>(555) 014-2290</span>
      </li>
      <li class="contacts__item">
        <svg class="contacts__icon" viewBox="0 0 20 20" aria-hidden="true">
          <circle cx="10" cy="10" r="10" fill="#111"/>
          <rect x="5" y="6.5" width="10" height="7" rx="1" fill="#fff"/>
          <path d="M5.3 7l4.7 3.6L14.7 7" stroke="#111" stroke-width="1.1" fill="none"/>
        </svg>
        <span>hello@brookvane.com</span>
      </li>
      <li class="contacts__item">
        <svg class="contacts__icon" viewBox="0 0 20 20" aria-hidden="true">
          <circle cx="10" cy="10" r="10" fill="#111"/>
          <g stroke="#fff" stroke-width="1.1" fill="none">
            <circle cx="10" cy="10" r="5"/>
            <ellipse cx="10" cy="10" rx="2.2" ry="5"/>
            <path d="M5 10h10"/>
          </g>
        </svg>
        <span>www.brookvane.com</span>
      </li>
    </ul>
    <p class="address">218 Harlow Ridge Road, Ocala, FL 34471</p>
  </section>

  <section class="card card--back" aria-label="Business card back">
    <div class="brand">
      <p class="brand__name">Brookvane Drafting</p>
    </div>
  </section>
</main>
</body>
</html>
```